Wordpress Theme for Medical Clinics

** Please view updated Sitemap2.pdf doc to clarify some confusion ***

This is a multiuser WordPress subscription site for medical clinics. Please see attachment for sitemap. Please do not include extra content like social media icons, search bars, or images. If you have questions, please ask for clarification.
The site contains the following pages and sub-pages:

1. Home
2. Our Clinic
2a. Our Clinic > Mission
2b. Our Clinic > Services
2c. Our Clinic > Clinic Policies
2d. Our Clinic > Schedules
3. Our Staff
3a. Our Staff > [Staff member page]
4. Resources
4a. Resources > Patient Health (index)
4b. Resources > Patient Health (index) > [post]
4c. Resources > Links
4d. Resources > Forms
5. Alerts
5a. Alerts > [Alert Page]
6. Contact Us

Includes the Following Pages, Subpages, and Content
1. Home
a. About Us
b. Our Staff
c. Bulletins
d. Accepting New Patients (shown as an alert widget)
e. Links
i. Physician Toolbox
ii. Book an Appointment
f. Clinic Policies
i. Show first 3 policies (e.g. Late Arrivals, Missed Appointments, Fees)
ii. Link to Clinic Policies page
g. Primary widget (displayed on all pages)
i. Hours of operation
ii. Contact Info
1. Tel
2. Fax
3. Email
4. Address
5. Get directions (link to Google Maps)
2. Our Clinic
a. Main Page
i. Clinic Name
ii. Overview
iii. Languages Spoken
iv. Secondary Navigation
1. Mission
2. Services
3. Clinic Policies
4. Schedules (see attachment)
b. Our Clinic > Mission
c. Our Clinic > Services
i. For each service include service TITLE and DESCRIPTION
d. Our Clinic > Clinic Policies
i. For each policy include policy TITLE and DESCRIPTION
ii. Include the following policies in mockup
1. Late arrivals
2. Missed appointments
3. Fees for missed appointments
4. Referrals and follow-ups
5. Services not covered by RDA
6. Information for LTF patients
7. Medical Legal Reports
e. Our Clinic > Schedules
3. Our Staff
a. Main Page
i. Display a list of staff members. Include NAME and DESIGNATION
b. Our Staff > [Staff Name]
i. Include NAME, PICTURE, DESIGNATION, and BIO
4. Resources
a. Resources > Patient Health
i. Main Page
1. Posts (ordered by date)
a. Title
b. Summary
2. Side Navigation
a. Post Categories
ii. Patient Health > [post title]
1. Title
2. Post Category
3. Date
4. Author
5. Summary
6. Body
b. Resources > Links
1. Secondary Navigation - Categories
a. Sample Categories:
i. Local Services
ii. RDA and Drug Coverage
iii. Mental Health Resources
2. Category page
a. Include the following links in the 'Local Services' category
i. Hypertension clinics
ii. Home Care services
iii. Vaccine Clinics
c. Resources > Forms
i. Display a table with form TITLE and CATEGORY
ii. Side Navigation
1. Form Categories
a. Use the following sample Categories
i. Referrals
ii. Insurance
iii. Intake
iv. Discharge
v. Waivers
5. Alerts
a. Main page
i. List of all Alert posts
1. Include post TITLE as a link to the post
ii. Side Navigation
1. Alerts Archive
a. shown as Month + Number of posts
iii. Alerts > [Alert page]
1. Include TITLE, DATE, AUTHOR, BODY
6. Contact Us
a. Map
b. Hours of operation
c. Address
d. Phone number
e. Fax number
e. Fax number
f. Map
g. Email

Design notes:
- fixed width
- responsive (need designs for mobile, tablet, and desktop)
- simple, dark font, white background
- use Font Awesome icons where needed
- user adds own logo

Target Market(s)

Medical Clinics

Industry/Entity Type

Medical

Number of Pages Required

5+ page

Font styles to use
Serif
Sans Serif

Requirements
Must have
• Please keep designs very simple.
• Examples:
• https://www.quolbin.com/install
• http://www.ventrohax.com/company/about-us
• http://brindlequota.org/
• http://www.trosk.com/
Should not have
• Minimal or no use of shadows and gradients

```html
<!DOCTYPE html>
<html lang="en">
<head>
<meta charset="utf-8">
<title>Harlow Clinics – Home</title>
<link href="https://fonts.googleapis.com/css2?family=Jost:wght@400;500;600&family=Open+Sans:wght@400;600;700&display=swap" rel="stylesheet">
<style>
:root{
  --navy:#0f3c6e;
  --sky:#29a9e0;
  --sky-soft:#7fcbef;
  --slate:#4f6f8f;
  --sun:#f9d44a;
  --leaf:#3aab48;
  --red:#d8262c;
  --text:#333;
  --muted:#5a7085;
  --panel:#f5f5f5;
  --rule:#e6e9ec;
}
*{box-sizing:border-box;margin:0;padding:0}
html,body{width:710px;height:1200px;overflow:hidden;background:#fff}
body{position:relative;font-family:"Open Sans",Arial,sans-serif;color:var(--text);font-size:6px;line-height:1.6}
.abs{position:absolute}
h1,h2,h3,.display{font-family:"Jost",Arial,sans-serif;font-weight:500;color:var(--navy)}

/* header */
.site-header{position:absolute;left:0;top:0;width:710px;height:58px}
.brand{left:66px;top:18px;display:flex;align-items:center;gap:6px}
.brand-mark{width:17px;height:17px;background:var(--sky);border-radius:3px}
.brand-name{font-family:"Jost",sans-serif;font-weight:500;font-size:21px;color:var(--navy);line-height:1}
.info{top:21px;font-size:6px;color:#555}
.info b{display:flex;align-items:center;gap:4px;color:var(--navy);font-weight:700;font-size:6.5px;margin-bottom:3px}
.info svg{width:6px;height:6px}
.info-divider{left:349px;top:20px;width:1px;height:26px;background:var(--rule)}
.menu-toggle{left:618px;top:26px}

/* hero */
.hero{left:0;top:58px;width:710px;height:245px;background:linear-gradient(90deg,#e9e4de 0%,#f3efe9 45%,#f8f8f6 75%,#fbfbfa 100%)}
.hero-arrow{top:164px;width:22px;height:22px;border-radius:50%;background:rgba(160,190,215,.8);display:flex;align-items:center;justify-content:center}
.hero-badge{left:469px;top:123px;width:158px;height:158px;border-radius:50%;background:var(--slate);color:#fff;text-align:center;padding:36px 26px 0}
.hero-badge h1{color:#fff;font-size:18px;line-height:1.2;margin-bottom:6px}
.hero-badge p{font-size:5.3px;line-height:1.65}
.btn-sun{display:inline-block;background:var(--sun);color:var(--navy);font-weight:700;font-size:5.5px;padding:4px 8px;border-radius:2px;letter-spacing:.1px}
.hero-badge .btn-sun{margin-top:11px}

/* new patients */
.np-title{left:65px;top:314px;font-size:14px}
.status-pill{left:65px;top:340px;border:1.5px solid #e2e2e2;border-radius:9px;padding:1px 7px 1px 5px;font-size:7px;display:flex;align-items:center;gap:4px;color:#333}
.dot{width:6px;height:6px;border-radius:50%;display:inline-block}
.legend{left:70px;top:369px;font-size:4.6px;display:flex;gap:6px;align-items:center}
.legend span{display:flex;align-items:center;gap:2px}
.legend .dot{width:4px;height:4px}
.patient{top:317px;display:flex;gap:6px}
.patient-photo{width:68px;height:58px}
.patient h3{font-size:8px;margin:13px 0 3px}
.patient p{font-size:5.5px;line-height:1.7;width:80px}

/* about */
.section-title{left:0;width:710px;text-align:center;font-size:14.5px}
.about-copy{left:66px;top:440px;width:579px;text-align:center;font-size:5.6px;line-height:2.15}
.about-copy p+p{margin-top:9px}

/* alerts */
.alerts-title{left:67px;top:545px;font-size:14px}
.pager{left:632px;top:548px;font-size:8px;color:#888;letter-spacing:2px}
.rule{height:1px;background:var(--rule)}
.alert{top:593px;display:flex;gap:10px}
.alert-date{width:28px;height:28px;background:var(--leaf);color:#fff;font-weight:700;font-size:6px;line-height:1.1;text-align:center;padding-top:3px}
.alert h4{font-size:5.8px;font-weight:700;color:var(--navy);line-height:1.95;width:130px}
.alert p{font-size:5.5px;color:var(--muted);line-height:2.1;width:130px;padding-left:2px}

/* staff */
.staff{top:749px;width:125px}
.staff .label{font-family:"Jost",sans-serif;font-weight:600;color:var(--navy);font-size:7.5px}
.staff h3{color:var(--sky);font-size:11px;font-weight:500;line-height:1.4}
.staff .role{font-weight:700;color:var(--navy);font-size:5.8px;margin-top:2px}
.staff p{font-size:5.6px;line-height:1.78;margin-top:9px}
.btn-sky{display:inline-block;background:var(--sky-soft);color:var(--navy);font-size:5.5px;padding:2px 11px;margin-top:11px}
.view-all{left:316px;top:909px;width:78px;text-align:center;padding:4px 0}

/* toolbox */
.toolbox{left:66px;top:977px;width:577px;height:126px;background:var(--panel)}
.toolbox-photo{left:3px;top:0;width:191px;height:126px;background:linear-gradient(135deg,#e3e8ec,#c9d6df 55%,#9bbad3)}
.toolbox h2{left:206px;top:25px;font-size:17.5px;font-weight:500;position:absolute}
.toolbox p{left:207px;top:57px;width:300px;font-size:5.6px;line-height:1.9;position:absolute}
.toolbox .btn-sky{position:absolute;left:207px;top:88px;margin:0;padding:2px 5px}

/* footer */
.site-footer{left:0;top:1136px;width:710px;height:64px;background:var(--panel);text-align:center}
.footer-nav{margin-top:22px;font-family:"Jost",sans-serif;font-weight:500;font-size:8px;color:#222}
.footer-nav span{margin:0 6px}
.copyright{margin-top:5px;font-family:"Jost",sans-serif;font-weight:500;font-size:8px;color:#222}
</style>
</head>
<body>

<header class="site-header">
  <div class="abs brand">
    <span class="brand-mark"></span>
    <span class="brand-name">Harlow Clinics</span>
  </div>
  <div class="abs info" style="left:275px">
    <b><svg viewBox="0 0 10 10"><path d="M2 1l2 2-1 1.5c.6 1.2 1.4 2 2.5 2.5L7 6l2 2-1.3 1.3C4.5 9 1 5.5.7 2.3z" fill="#f0b400"/></svg>Telephone</b>
    +49 30 5550 1182
  </div>
  <div class="abs info-divider"></div>
  <div class="abs info" style="left:356px">
    <b><svg viewBox="0 0 10 10"><circle cx="5" cy="5" r="4" fill="none" stroke="#f0b400" stroke-width="1.3"/><path d="M5 2.6V5l1.6 1" stroke="#f0b400" stroke-width="1.1" fill="none"/></svg>Hours of Operation</b>
    Mon- Sat 8:30am to 5:00pm &nbsp;&nbsp;|&nbsp;&nbsp; Sun - Holiday
  </div>
  <svg class="abs menu-toggle" width="11" height="9" viewBox="0 0 11 9"><rect width="11" height="1.8" fill="#29a9e0"/><rect y="3.6" width="11" height="1.8" fill="#29a9e0"/><rect y="7.2" width="11" height="1.8" fill="#29a9e0"/></svg>
</header>

<section>
  <div class="abs hero" role="img" aria-label="Photo of a smiling young physician with an older female patient"></div>
  <div class="abs hero-arrow" style="left:35px"><svg width="8" height="10" viewBox="0 0 8 10"><path d="M6 1L2 5l4 4" stroke="#fff" stroke-width="2" fill="none"/></svg></div>
  <div class="abs hero-arrow" style="left:651px"><svg width="8" height="10" viewBox="0 0 8 10"><path d="M2 1l4 4-4 4" stroke="#fff" stroke-width="2" fill="none"/></svg></div>
  <div class="abs hero-badge">
    <h1>Harlow Clinics</h1>
    <p>Lorem Ipsum is simply dummy text of the printing and typesetting industry. Lorem Ipsum has been the industry's standard dummy text ever</p>
    <span class="btn-sun">BOOK AN APPOINTMENT</span>
  </div>
</section>

<section>
  <h2 class="abs np-title">New Patients</h2>
  <div class="abs status-pill"><span class="dot" style="background:var(--leaf)"></span>Available</div>
  <div class="abs legend"><span><i class="dot" style="background:var(--leaf)"></i>Accepting</span><span><i class="dot" style="background:var(--red)"></i>Not Accepting</span></div>

  <div class="abs patient" style="left:170px">
    <div class="patient-photo" role="img" aria-label="Portrait photo of a young woman" style="background:linear-gradient(135deg,#6b5446,#b89a86)"></div>
    <div><h3>Patient 1</h3><p>Lorem Ipsum is simply dummy text of the printing</p></div>
  </div>
  <div class="abs patient" style="left:325px">
    <div class="patient-photo" role="img" aria-label="Photo of an older woman with a doctor" style="background:linear-gradient(135deg,#a9c6dc,#e4e6ea)"></div>
    <div><h3>Patient 1</h3><p>Lorem Ipsum is simply dummy text of the printing</p></div>
  </div>
  <div class="abs patient" style="left:485px">
    <div class="patient-photo" role="img" aria-label="Portrait photo of a smiling older man" style="background:linear-gradient(135deg,#c9b4a6,#dfe4ea)"></div>
    <div><h3>Patient 1</h3><p>Lorem Ipsum is simply dummy text of the printing</p></div>
  </div>
</section>

<section>
  <h2 class="abs section-title" style="top:406px">About Us</h2>
  <div class="abs about-copy">
    <p>Lorem Ipsum is simply dummy text of the printing and typesetting industry. Lorem Ipsum has been the industry's standard dummy text ever since the 1500s, when an unknown printer took a galley of type and scrambled it to make a type specimen book. It has survived not only five centuries, but also the leap into electronic typesetting, remaining essentially unchanged. It was popularised in the 1960s with the release of Letraset sheets containing Lorem Ipsum passages, and more recently with desktop publishing software like Aldus PageMaker including versions of Lorem Ipsum.</p>
    <p>Lorem Ipsum is simply dummy text of the printing and typesetting industry. Lorem Ipsum has been the industry's standard dummy text ever since the 1500s.</p>
  </div>
</section>

<section>
  <h2 class="abs alerts-title">Alerts/Bulletins</h2>
  <div class="abs pager">‹ ›</div>
  <div class="abs rule" style="left:66px;top:575px;width:578px"></div>
  <article class="abs alert" style="left:66px">
    <div class="alert-date">June<br>6th<br>2015</div>
    <div><h4>Lorem Ipsum is simply dummy text of the printing and typesetting industry.</h4><p>Lorem Ipsum has been the industry's standard dummy text ever since the 1500s</p></div>
  </article>
  <article class="abs alert" style="left:264px">
    <div class="alert-date">June<br>6th<br>2015</div>
    <div><h4>Lorem Ipsum is simply dummy text of the printing and typesetting industry.</h4><p>Lorem Ipsum has been the industry's standard dummy text ever since the 1500s</p></div>
  </article>
  <article class="abs alert" style="left:462px">
    <div class="alert-date">June<br>6th<br>2015</div>
    <div><h4>Lorem Ipsum is simply dummy text of the printing and typesetting industry.</h4><p>Lorem Ipsum has been the industry's standard dummy text ever since the 1500s</p></div>
  </article>
</section>

<section>
  <h2 class="abs section-title" style="top:680px">Staff</h2>
  <div class="abs rule" style="left:66px;top:721px;width:578px"></div>
  <div class="abs staff" style="left:65px"><div class="label">Staff 1</div><h3>Daniel Forsythe</h3><div class="role">Physician</div><p>Lorem Ipsum is simply dummy text of the printing and typesetting industry. Lorem Ipsum has been the industry's standard dummy text ever since the 1500s, when an unknown printer took</p><span class="btn-sky">More</span></div>
  <div class="abs staff" style="left:214px"><div class="label">Staff 1</div><h3>Daniel Forsythe</h3><div class="role">Physician</div><p>Lorem Ipsum is simply dummy text of the printing and typesetting industry. Lorem Ipsum has been the industry's standard dummy text ever since the 1500s, when an unknown printer took</p><span class="btn-sky">More</span></div>
  <div class="abs staff" style="left:362px"><div class="label">Staff 1</div><h3>Daniel Forsythe</h3><div class="role">Physician</div><p>Lorem Ipsum is simply dummy text of the printing and typesetting industry. Lorem Ipsum has been the industry's standard dummy text ever since the 1500s, when an unknown printer took</p><span class="btn-sky">More</span></div>
  <div class="abs staff" style="left:510px"><div class="label">Staff 1</div><h3>Daniel Forsythe</h3><div class="role">Physician</div><p>Lorem Ipsum is simply dummy text of the printing and typesetting industry. Lorem Ipsum has been the industry's standard dummy text ever since the 1500s, when an unknown printer took</p><span class="btn-sky">More</span></div>
  <span class="abs btn-sun view-all">VIEW ALL STAFF</span>
</section>

<section class="abs toolbox">
  <div class="abs toolbox-photo" role="img" aria-label="Photo of a smiling nurse in blue scrubs holding a tablet"></div>
  <h2>Physician Toolbox</h2>
  <p>Lorem Ipsum is simply dummy text of the printing and typesetting industry. Lorem Ipsum has been the industry's standard dummy text ever since the 1500s, when an unknown printer took</p>
  <span class="btn-sky">Read More</span>
</section>

<footer class="abs site-footer">
  <nav class="footer-nav">Home<span>|</span>Clinic<span>|</span>Our Staff<span>|</span>Resources<span>|</span>Contact Us</nav>
  <div class="copyright">© 2015 Company Name , All Rights Reserved</div>
</footer>

</body>
</html>
```